Human Resource Consulting practice needs a business card design

We need a business card design (double sided colour) for our Human Resource (HR) consulting practice in regional New South Wales, australia. Our business name is Staff Compass. We support small and medium business across the Mid North Coast of New South Wales by providing them with outsourced HR support, services and products to help them achieve compliance with workplace legislation and across all areas of the employment lifecycle from recruitment to termination and everything in between. Our corporate colours are hot pink and black. The final design should communicate professionalism, trust, people focus.
I have attached the current (old) business card for your reference.

Target Market(s)

Business owners and high level managers

Industry/Entity Type

Business

Contact Information for Business Card

Name
Title
Phone no
Mobile no
Address
PO Box
email address
website

Colors
e34197

Requirements
Must have
• Tempate for changing business card personal details including Name, position title, mobile number, email address.
• Keep current logo and colours as per attached
• Logo must be presented in 2 colours or black only not white
Nice to have
• One side logo and graphic only other side logo and personal details
Should not have
• Should not be the same as the current version (attached) but a modern interpretation.
• Does not need a busy reverse side with our list of services as per current version. I feel this is too busy.
• No photos

```html
<!DOCTYPE html>
<html lang="en">
<head>
<meta charset="utf-8">
<title>Staff Compass – Business Card</title>
<link rel="stylesheet" href="https://fonts.googleapis.com/css2?family=Archivo+Black&family=Michroma&display=swap">
<style>
  :root {
    --bg: #2a2a2a;
    --pink: #ec0c8e;
    --ink: #262626;
    --white: #ffffff;
  }
  * { box-sizing: border-box; margin: 0; padding: 0; }
  html, body { width: 1200px; height: 1189px; overflow: hidden; background: var(--bg); }
  .canvas { position: relative; width: 1200px; height: 1189px; }
  .card {
    position: absolute; left: 160px; width: 880px; height: 503px;
    background: var(--pink); border-radius: 22px; overflow: hidden;
  }
  .card--front { top: 52px; }
  .card--back { top: 634px; }

  .brand-dot { width: 26px; height: 26px; border-radius: 50%; background: var(--ink); flex: none; }
  .brand-name {
    font-family: "Archivo Black", sans-serif; line-height: 1;
    color: var(--ink); letter-spacing: -1px; white-space: nowrap;
  }

  /* front */
  .front-brand {
    position: absolute; top: 170px; left: 0; right: 0;
    display: flex; align-items: center; justify-content: center; gap: 18px;
  }
  .front-brand .brand-name { font-size: 74px; }
  .front-url {
    position: absolute; top: 318px; left: 0; right: 0;
    display: flex; align-items: center; justify-content: center; gap: 22px;
  }
  .front-url .rule { width: 150px; height: 1px; background: var(--white); opacity: .85; }
  .front-url .url { font-family: "Michroma", sans-serif; font-size: 17px; color: var(--white); letter-spacing: 1px; }

  /* back */
  .back-brand {
    position: absolute; top: 64px; left: 54px;
    display: flex; align-items: center; gap: 12px;
  }
  .back-brand .brand-dot { width: 20px; height: 20px; }
  .back-brand .brand-name { font-size: 52px; }
  .person { position: absolute; top: 134px; right: 54px; text-align: right; }
  .person-name { font-family: "Archivo Black", sans-serif; font-size: 32px; line-height: 1.1; color: var(--white); letter-spacing: 1px; }
  .person-title { font-family: "Michroma", sans-serif; font-size: 14px; color: var(--ink); letter-spacing: 1px; margin-top: 6px; }
  .divider { position: absolute; top: 226px; left: 54px; right: 54px; height: 1px; background: var(--white); opacity: .85; }
  .contacts { position: absolute; top: 270px; left: 54px; list-style: none; }
  .contacts li {
    display: flex; align-items: center; gap: 20px; height: 46px;
    font-family: "Michroma", sans-serif; font-size: 20px; color: var(--ink); letter-spacing: 1px;
  }
  .contacts svg { width: 30px; height: 30px; flex: none; }
  .address {
    position: absolute; top: 262px; right: 54px; text-align: right; font-style: normal;
    font-family: "Michroma", sans-serif; font-size: 20px; line-height: 1.6; color: var(--ink); letter-spacing: 1px;
  }
</style>
</head>
<body>
<main class="canvas">
  <section class="card card--front" aria-label="Card front">
    <div class="front-brand">
      <span class="brand-dot"></span>
      <span class="brand-name">Staff Compass</span>
    </div>
    <div class="front-url">
      <span class="rule"></span>
      <span class="url">www.staffcompass.com.au</span>
      <span class="rule"></span>
    </div>
  </section>

  <section class="card card--back" aria-label="Card back">
    <div class="back-brand">
      <span class="brand-dot"></span>
      <span class="brand-name">Staff Compass</span>
    </div>
    <div class="person">
      <p class="person-name">Megan Holt</p>
      <p class="person-title">PRINCIPAL CONSULTANT</p>
    </div>
    <div class="divider"></div>
    <ul class="contacts">
      <li>
        <svg viewBox="0 0 30 30" aria-hidden="true"><rect width="30" height="30" rx="5" fill="#fff"/><path d="M9 8c2-1 3 0 4 3l-2 2c1 2 3 4 5 5l2-2c3 1 4 2 3 4-1 2-3 3-6 1-3-2-6-5-7-8-1-2 0-4 1-5z" fill="#ec0c8e"/></svg>
        02 5550 4182
      </li>
      <li>
        <svg viewBox="0 0 30 30" aria-hidden="true"><rect width="30" height="30" rx="5" fill="#fff"/><rect x="10" y="6" width="10" height="18" rx="2" fill="none" stroke="#ec0c8e" stroke-width="2"/><rect x="12" y="9" width="6" height="7" fill="#ec0c8e"/></svg>
        0400 555 271
      </li>
      <li>
        <svg viewBox="0 0 30 30" aria-hidden="true"><rect width="30" height="30" rx="5" fill="#fff"/><rect x="6" y="9" width="18" height="12" fill="none" stroke="#ec0c8e" stroke-width="2"/><path d="M6 9l9 7 9-7" fill="none" stroke="#ec0c8e" stroke-width="2"/></svg>
        megan@staffcompass.com.au
      </li>
      <li>
        <svg viewBox="0 0 30 30" aria-hidden="true"><rect width="30" height="30" rx="5" fill="#fff"/><circle cx="15" cy="15" r="8" fill="none" stroke="#ec0c8e" stroke-width="2"/><path d="M7 15h16M15 7c-4 5-4 11 0 16M15 7c4 5 4 11 0 16" fill="none" stroke="#ec0c8e" stroke-width="1.5"/></svg>
        www.staffcompass.com.au
      </li>
    </ul>
    <address class="address">P.O. Box 218<br>Kellan Heads, NSW 2400</address>
  </section>
</main>
</body>
</html>
```